Brand Identity Stationary Package

Hello I'm looking for a full branding package for my Property Management Company. I have a logo but looking to have the following
Business Card
Email signature
Facebook cover photo
Letterhead (word.doc)
#10 Envelope
Pocket Folder - link to 9x12 pocket folder design specs https://www.printorbit-example.ca/marketing-materials/presentation-folders
would like everything to match and be brand identifiable. The company looks after residential properties/apartments and some commercial properties. Attached is a zip of the files.
For Business Card
Name: Gareth Lindqvist
Position: Operations Manager
Number: 1 (555) 384-2917
Email: Gareth@harborkey-example.ca
Website: Harborkey-example.ca
Property Management

```html
<!DOCTYPE html>
<html lang="en">
<head>
<meta charset="utf-8">
<title>Harborkey Stationery Package</title>
<link rel="stylesheet" href="https://fonts.googleapis.com/css2?family=Montserrat:wght@600&family=Open+Sans:wght@400;600&family=Roboto+Condensed:wght@400&display=swap">
<style>
  :root {
    --bg: #c4c4c4;
    --paper: #f2f2f2;
    --paper-shade: #e4e4e4;
    --ink: #1d1d1d;
    --ink-soft: #2a2a2a;
    --green: #7ab342;
    --text-grey: #555;
  }
  * { box-sizing: border-box; margin: 0; padding: 0; }
  html, body { width: 1200px; height: 800px; overflow: hidden; }
  body {
    background: linear-gradient(180deg, #cfcfcf 0%, var(--bg) 100%);
    position: relative;
    font-family: "Open Sans", sans-serif;
    color: var(--ink);
  }
  .piece { position: absolute; box-shadow: 0 2px 6px rgba(0,0,0,.18); }
  .brand-name {
    font-family: "Montserrat", sans-serif;
    font-weight: 600;
    letter-spacing: .08em;
    line-height: 1;
    white-space: nowrap;
  }
  .brand-name--dark { color: var(--ink); }
  .brand-name--light { color: #fff; }

  /* Pocket folder, open */
  .folder-open { left: 240px; top: 83px; width: 455px; height: 304px; background: var(--paper); box-shadow: 0 3px 8px rgba(0,0,0,.2); }
  .folder-open__fold { position: absolute; left: 227px; top: 0; width: 1px; height: 100%; background: #cfcfcf; }
  .folder-open__pockets { position: absolute; left: 0; top: 204px; width: 455px; height: 100px; }

  /* Pocket folder, cover */
  .folder-cover { left: 727px; top: 80px; width: 226px; height: 304px; background: var(--ink); }
  .folder-cover .brand-name { position: absolute; left: 0; right: 0; top: 140px; text-align: center; font-size: 20px; }
  .folder-cover__web { position: absolute; left: 0; right: 0; bottom: 18px; text-align: center; font-family: "Roboto Condensed", sans-serif; font-size: 7px; color: #ddd; }

  /* Poster tube wrap, flat */
  .tube-wrap { left: 983px; top: 80px; width: 63px; height: 560px; background: linear-gradient(90deg, #111 0%, #333 40%, #1a1a1a 100%); }
  .tube-wrap__band { position: absolute; left: 0; top: 353px; width: 63px; height: 172px; background: linear-gradient(90deg, #e6e6e6, #fafafa 45%, #e2e2e2); }
  .tube-wrap__band .brand-name { position: absolute; left: 50%; top: 50%; transform: translate(-50%, -50%) rotate(-90deg); font-size: 17px; }

  /* Envelopes */
  .envelope { width: 218px; background: var(--paper); overflow: hidden; }
  .envelope__photo { position: absolute; right: 0; top: 0; width: 76px; height: 100%; background: linear-gradient(180deg, #e9e9e9, #dcdcdc 60%, #e6e6e6); opacity: .8; }
  .envelope__band { position: absolute; left: 0; bottom: 0; width: 100%; height: 4px; }
  .envelope__return { position: absolute; left: 13px; top: 15px; }
  .envelope__return .brand-name { font-size: 10px; }
  .envelope__address { font-family: "Roboto Condensed", sans-serif; font-size: 5px; line-height: 1.3; color: var(--text-grey); margin-top: 4px; text-align: center; }
  .envelope-front--left { left: 248px; top: 572px; height: 108px; }
  .envelope-front--right { left: 723px; top: 410px; height: 109px; }
  .envelope-back { height: 149px; }
  .envelope-back--open { left: 248px; top: 408px; background: transparent; box-shadow: none; overflow: visible; }
  .envelope-back--closed { left: 723px; top: 531px; height: 109px; }
  .envelope-back--closed .brand-name { position: absolute; left: 0; right: 0; top: 17px; text-align: center; font-size: 10px; }

  /* Letterhead */
  .letterhead { left: 487px; top: 406px; width: 208px; height: 294px; background: #fafafa; }
  .letterhead__head { position: absolute; left: 21px; top: 26px; right: 21px; display: flex; justify-content: space-between; }
  .letterhead__head .brand-name { font-size: 10px; margin-top: 5px; }
  .letterhead__contact { font-family: "Roboto Condensed", sans-serif; font-size: 3.6px; line-height: 1.45; color: var(--text-grey); }
  .contact-line { display: flex; align-items: center; gap: 2px; }
  .contact-line svg { width: 3.5px; height: 3.5px; flex: none; }
  .letterhead__body { position: absolute; left: 21px; right: 21px; top: 75px; font-size: 3.6px; line-height: 1.5; color: var(--text-grey); text-align: justify; }
  .letterhead__body p { margin-bottom: 3.5px; }
  .letterhead__signature { position: absolute; left: 21px; top: 219px; width: 24px; height: 20px; background: linear-gradient(135deg, #eee, #e4e4e4); }
  .letterhead__band { position: absolute; left: 0; bottom: 0; width: 100%; height: 4px; }

  /* Business cards */
  .card { top: 659px; width: 85px; height: 54px; }
  .card--front { left: 722px; background: #fafafa; }
  .card--front .brand-name { position: absolute; left: 8px; top: 24px; font-size: 5.5px; }
  .card__rule { position: absolute; left: 45px; top: 14px; width: .5px; height: 26px; background: var(--green); }
  .card__details { position: absolute; left: 48px; top: 14px; font-family: "Roboto Condensed", sans-serif; font-size: 2.4px; line-height: 1.4; color: var(--text-grey); }
  .card__name { color: var(--green); font-weight: 600; font-size: 2.8px; text-transform: uppercase; }
  .card__role { color: var(--ink); margin-bottom: 1.5px; }
  .card__band { position: absolute; left: 0; bottom: 0; width: 100%; height: 2px; }
  .card--back { left: 821px; background: var(--ink); }
  .card--back .brand-name { position: absolute; left: 0; right: 0; top: 19px; text-align: center; font-size: 9px; }
  .card__web { position: absolute; left: 0; right: 0; bottom: 7px; text-align: center; font-family: "Roboto Condensed", sans-serif; font-size: 3px; color: #ccc; }
</style>
</head>
<body>

<!-- Pocket folder, inside spread -->
<div class="piece folder-open">
  <div class="folder-open__fold"></div>
  <svg class="folder-open__pockets" viewBox="0 0 455 100" aria-hidden="true">
    <path d="M0 0 H204 Q214 0 214 12 L222 100 H0 Z" fill="#1d1d1d"/>
    <path d="M455 0 H252 Q242 0 241 12 L233 100 H455 Z" fill="#1d1d1d"/>
  </svg>
</div>

<!-- Pocket folder, cover -->
<div class="piece folder-cover">
  <div class="brand-name brand-name--light">HARBORKEY</div>
  <div class="folder-cover__web">www.harborkey-example.ca</div>
</div>

<!-- Poster tube wrap -->
<div class="piece tube-wrap">
  <div class="tube-wrap__band">
    <div class="brand-name brand-name--dark">HARBORKEY</div>
  </div>
</div>

<!-- Envelope back, flap open -->
<div class="piece envelope envelope-back envelope-back--open">
  <svg width="218" height="149" viewBox="0 0 218 149" aria-hidden="true">
    <path d="M5 0 H213 L218 40 H0 Z" fill="#1d1d1d"/>
    <rect x="0" y="40" width="218" height="109" fill="#f0f0f0"/>
    <path d="M14 40 H204 V64 H14 Z" fill="#2a2a2a"/>
    <path d="M0 40 L14 48 V64 L0 149 Z" fill="#e6e6e6"/>
    <path d="M218 40 L204 48 V64 L218 149 Z" fill="#e6e6e6"/>
  </svg>
</div>

<!-- Envelope front, left -->
<div class="piece envelope envelope-front--left">
  <div class="envelope__photo" role="img" aria-label="Faint photo of a residential building"></div>
  <div class="envelope__return">
    <div class="brand-name brand-name--dark">HARBORKEY</div>
    <div class="envelope__address">Unit 7 / 88 Harbour Lane,<br>Westvale, NSW 2199</div>
  </div>
  <svg class="envelope__band" viewBox="0 0 218 4" preserveAspectRatio="none" aria-hidden="true">
    <rect width="218" height="4" fill="#1d1d1d"/>
    <path d="M32 0 H218 V3 H36 Z" fill="#7ab342"/>
  </svg>
</div>

<!-- Letterhead -->
<div class="piece letterhead">
  <div class="letterhead__head">
    <div class="brand-name brand-name--dark">HARBORKEY</div>
    <div class="letterhead__contact">
      <div>14 Cedar Bluff Road,</div>
      <div>Maple Grove, ON L5T 3K8</div>
      <div class="contact-line"><svg viewBox="0 0 10 10"><path d="M2 1 L4 1 L5 3 L4 4 Q5 6 6 6 L7 5 L9 6 L9 8 Q5 9 2 5 Q1 3 2 1Z" fill="#7ab342"/></svg>1 (555) 384-2917</div>
      <div class="contact-line"><svg viewBox="0 0 10 10"><rect x="1" y="2" width="8" height="6" fill="#7ab342"/></svg>Gareth@harborkey-example.ca</div>
      <div class="contact-line"><svg viewBox="0 0 10 10"><circle cx="5" cy="5" r="4" fill="none" stroke="#7ab342" stroke-width="1.4"/></svg>www.harborkey-example.ca</div>
    </div>
  </div>
  <div class="letterhead__body">
    <p>Dear customer,</p>
    <p>Lorem ipsum dolor sit amet, consectetur adipisicing elit, sed do eiusmod tempor incididunt ut labore et dolore magna aliqua. Ut enim ad minim veniam, quis nostrud exercitation ullamco laboris nisi ut aliquip ex ea commodo consequat. Duis aute irure dolor in reprehenderit in voluptate velit esse cillum dolore eu fugiat nulla pariatur. Excepteur sint occaecat cupidatat non proident, sunt in culpa qui officia deserunt mollit anim id est laborum.</p>
    <p>Lorem ipsum dolor sit amet, consectetur adipisicing elit, sed do eiusmod tempor incididunt ut labore et dolore magna aliqua. Ut enim ad minim veniam, quis nostrud exercitation ullamco laboris nisi ut aliquip ex ea commodo consequat. Duis aute irure dolor in reprehenderit in voluptate velit esse cillum dolore eu fugiat nulla pariatur. Excepteur sint occaecat cupidatat non proident, sunt in culpa qui officia deserunt mollit anim id est laborum.</p>
    <p>Lorem ipsum dolor sit amet, consectetur adipisicing elit, sed do eiusmod tempor incididunt ut labore et dolore magna aliqua. Ut enim ad minim veniam, quis nostrud exercitation ullamco laboris nisi ut aliquip ex ea commodo consequat. Duis aute irure dolor in reprehenderit in voluptate velit esse cillum dolore eu fugiat nulla pariatur. Excepteur sint occaecat cupidatat non proident, sunt in culpa qui officia deserunt mollit anim id est laborum.</p>
    <p>Lorem ipsum dolor sit amet, consectetur adipisicing elit, sed do eiusmod tempor incididunt ut labore et dolore magna aliqua. Ut enim ad minim veniam, quis nostrud exercitation ullamco laboris nisi ut aliquip ex ea commodo consequat. Duis aute irure dolor in reprehenderit.</p>
    <p>Yours Sincerely,</p>
  </div>
  <div class="letterhead__signature" role="img" aria-label="Handwritten signature"></div>
  <svg class="letterhead__band" viewBox="0 0 208 4" preserveAspectRatio="none" aria-hidden="true">
    <rect width="208" height="4" fill="#1d1d1d"/>
    <path d="M32 0 H208 V3 H36 Z" fill="#7ab342"/>
  </svg>
</div>

<!-- Envelope front, right -->
<div class="piece envelope envelope-front--right">
  <div class="envelope__photo" role="img" aria-label="Faint photo of a residential building"></div>
  <div class="envelope__return">
    <div class="brand-name brand-name--dark">HARBORKEY</div>
    <div class="envelope__address">Unit 7 / 88 Harbour Lane,<br>Westvale, NSW 2199</div>
  </div>
  <svg class="envelope__band" viewBox="0 0 218 4" preserveAspectRatio="none" aria-hidden="true">
    <rect width="218" height="4" fill="#1d1d1d"/>
    <path d="M32 0 H218 V3 H36 Z" fill="#7ab342"/>
  </svg>
</div>

<!-- Envelope back, flap closed -->
<div class="piece envelope envelope-back--closed">
  <svg width="218" height="109" viewBox="0 0 218 109" style="position:absolute;left:0;top:0" aria-hidden="true">
    <path d="M0 0 H218 L212 36 Q210 42 200 42 H12 Q4 42 3 48 L0 0 Z" fill="#1d1d1d"/>
    <path d="M0 48 L3 48 L0 109 Z" fill="#e2e2e2"/>
  </svg>
  <div class="brand-name brand-name--light">HARBORKEY</div>
</div>

<!-- Business card, front -->
<div class="piece card card--front">
  <div class="brand-name brand-name--dark">HARBORKEY</div>
  <div class="card__rule"></div>
  <div class="card__details">
    <div class="card__name">Gareth Lindqvist</div>
    <div class="card__role">Operations Manager</div>
    <div>14 Cedar Bluff Road,</div>
    <div>Maple Grove, ON L5T 3K8</div>
    <div>1 (555) 384-2917</div>
    <div>Gareth@harborkey-example.ca</div>
    <div>harborkey-example.ca</div>
  </div>
  <svg class="card__band" viewBox="0 0 85 2" preserveAspectRatio="none" aria-hidden="true">
    <rect width="85" height="2" fill="#1d1d1d"/>
    <path d="M18 0 H85 V2 H20 Z" fill="#7ab342"/>
  </svg>
</div>

<!-- Business card, back -->
<div class="piece card card--back">
  <div class="brand-name brand-name--light">HARBORKEY</div>
  <div class="card__web">www.harborkey-example.ca</div>
</div>

</body>
</html>
```